BildeVOLD buisnesscard

Hey :) I need a modern buisnesscard for my company BildeVOLD
It most have:
Dagligleder og Fotograf: Henrik Audun Strandvik

Mob: +4791264085
Epost: post@bildevold.example
Adresse: Kvernbakken9, 6040 Langevåg

Facbook and instagram logo with text BildeVOLD

BildeVOLD logo

It Company

```html
<!DOCTYPE html>
<html lang="no">
<head>
<meta charset="UTF-8">
<title>BildeVOLD – visittkort</title>
<link rel="stylesheet" href="https://fonts.googleapis.com/css2?family=Exo+2:wght@700&family=Open+Sans:wght@400;600&display=swap">
<style>
  :root {
    --backdrop: #4a4a4a;
    --card-white: #ffffff;
    --brand-blue: #2680bb;
    --brand-blue-light: #3f95cb;
    --brand-blue-dark: #1d6ea5;
    --brand-pink: #c94788;
    --brand-pink-light: #e07bb0;
    --text-light: #ffffff;
  }
  * { box-sizing: border-box; margin: 0; padding: 0; }
  html, body { width: 1200px; height: 950px; overflow: hidden; }
  body {
    background: var(--backdrop);
    display: flex;
    align-items: center;
    justify-content: center;
    gap: 64px;
  }
  .card {
    width: 480px;
    height: 760px;
    position: relative;
    overflow: hidden;
    box-shadow: 0 10px 30px rgba(0,0,0,.35);
  }

  /* Front */
  .card--front { background: var(--card-white); }
  .info-panel {
    position: absolute;
    top: 0; left: 26px; right: 26px;
    height: 400px;
    background: linear-gradient(135deg, var(--brand-blue-light), var(--brand-blue) 55%, var(--brand-blue-dark));
    clip-path: polygon(0 0, 100% 0, 100% 70%, 76% 100%, 24% 100%, 0 70%);
    color: var(--text-light);
    text-align: center;
    padding-top: 44px;
  }
  .person-name {
    font-family: 'Exo 2', sans-serif;
    font-weight: 700;
    font-size: 27px;
    letter-spacing: .5px;
  }
  .person-role {
    font-family: 'Exo 2', sans-serif;
    font-weight: 700;
    font-size: 19px;
    margin-top: 6px;
  }
  .divider {
    border: none;
    border-top: 1.5px dotted rgba(255,255,255,.75);
    width: 78%;
    margin: 16px auto;
  }
  .address {
    font-family: 'Open Sans', sans-serif;
    font-size: 18px;
  }
  .contact-list {
    list-style: none;
    font-family: 'Open Sans', sans-serif;
    font-size: 18px;
    line-height: 1.5;
  }
  .contact-list li {
    display: flex;
    align-items: center;
    justify-content: center;
    gap: 8px;
  }
  .contact-list svg { width: 16px; height: 16px; fill: var(--text-light); }
  .social {
    display: flex;
    justify-content: center;
    gap: 12px;
    margin-top: 14px;
  }
  .social-dot {
    width: 26px; height: 26px;
    border-radius: 50%;
    background: var(--text-light);
  }
  .brand-name {
    font-family: 'Exo 2', sans-serif;
    font-weight: 700;
  }
  .card--front .brand-name {
    position: absolute;
    top: 500px; left: 0; right: 0;
    text-align: center;
    font-size: 64px;
    color: var(--brand-blue);
  }
  .pink-band {
    position: absolute;
    left: 0; right: 0; bottom: 0;
    height: 46px;
    background: var(--brand-pink);
  }
  .pink-band::before {
    content: "";
    position: absolute;
    left: 0; top: 0; bottom: 0;
    width: 38%;
    background: var(--brand-pink-light);
  }

  /* Back */
  .card--back {
    background: var(--brand-pink);
    display: flex;
    align-items: center;
    justify-content: center;
  }
  .card--back .brand-name {
    font-size: 66px;
    color: var(--text-light);
  }
</style>
</head>
<body>
  <section class="card card--front">
    <div class="info-panel">
      <h1 class="person-name">Henrik Audun Strandvik</h1>
      <p class="person-role">Dagligleder og Fotograf</p>
      <hr class="divider">
      <p class="address">Kvernbakken9, 6040 Langevåg</p>
      <hr class="divider">
      <ul class="contact-list">
        <li><svg viewBox="0 0 16 16" aria-hidden="true"><path d="M4 0h8a1 1 0 0 1 1 1v14a1 1 0 0 1-1 1H4a1 1 0 0 1-1-1V1a1 1 0 0 1 1-1zm0 2v11h8V2zm4 11.6a.8.8 0 1 0 0 1.6.8.8 0 0 0 0-1.6z"/></svg>+4791264085</li>
        <li><svg viewBox="0 0 16 16" aria-hidden="true"><path d="M1 3h14v10H1zm1.2 1.2L8 8.6l5.8-4.4z"/></svg>post@bildevold.example</li>
        <li><svg viewBox="0 0 16 16" aria-hidden="true"><circle cx="8" cy="8" r="7.2" fill="none" stroke="#fff" stroke-width="1.6"/><path d="M1 8h14M8 1c-2.5 2.2-2.5 11.8 0 14M8 1c2.5 2.2 2.5 11.8 0 14" fill="none" stroke="#fff" stroke-width="1.2"/></svg>www.bildevold.example</li>
      </ul>
      <div class="social" aria-label="Sosiale medier">
        <span class="social-dot" aria-hidden="true"></span>
        <span class="social-dot" aria-hidden="true"></span>
      </div>
    </div>
    <p class="brand-name">BildeVOLD</p>
    <div class="pink-band"></div>
  </section>

  <section class="card card--back">
    <p class="brand-name">BildeVOLD</p>
  </section>
</body>
</html>
```